BLPR Postcard Design: Mosquito Control, Lawn Maintenance and Pressure washing

I have a new company based in Atlanta,Georgia named Birchfield Lawn Pest Relief, LLC. We specializes in Mosquito Control. We also have additional services: Lawn maintenance, Pressure Washing and Gutter Cleaning. I would like to see designs with the colors Black, Red, Gray. We would like the customer to think of us when it comes to Enjoying a mosquito free yard and improving the look and feel of their home and lawn.

Industry/Entity Type

It Company

Requirements
Nice to have
• Treatment plans starting at $69/mt - front of card
• The additional services we offer - back of card.

```html
<!DOCTYPE html>
<html lang="en">
<head>
<meta charset="utf-8">
<title>BLPR Postcard – Additional Services</title>
<link rel="stylesheet" href="https://fonts.googleapis.com/css2?family=Abril+Fatface&family=PT+Sans:wght@400;700&family=PT+Serif:wght@700&display=swap">
<style>
  :root {
    --red-top: #8e1a12;
    --red-mid: #5a110c;
    --black: #0d0d0d;
    --gray-light: #a9a9a9;
    --gray-mid: #7d7d7d;
    --gray-dark: #2e2e2e;
    --box-fill: #4a4a4a;
    --box-line: #c9c9c9;
    --white: #ffffff;
    --brand-red: #e0241b;
    --address-fill: #a8a8a8;
    --address-line: #1e1e1e;
  }
  html, body {
    margin: 0;
    padding: 0;
    overflow: hidden;
    background: #ffffff;
  }
  .postcard {
    position: relative;
    width: 1200px;
    height: 779px;
    overflow: hidden;
    font-family: "PT Sans", Arial, sans-serif;
  }
  .services-panel {
    position: absolute;
    left: 0; top: 0;
    width: 690px; height: 779px;
    background: linear-gradient(180deg, var(--red-top) 0%, var(--red-mid) 38%, #2a0c0a 70%, var(--black) 100%);
  }
  .mailing-panel {
    position: absolute;
    left: 690px; top: 0;
    width: 510px; height: 779px;
    background: linear-gradient(180deg, var(--gray-light) 0%, var(--gray-mid) 45%, var(--gray-dark) 100%);
  }
  .services-title {
    position: absolute;
    left: 0; top: 30px;
    width: 690px;
    margin: 0;
    text-align: center;
    font-family: "Abril Fatface", Georgia, serif;
    font-weight: 400;
    font-size: 45px;
    line-height: 56px;
    letter-spacing: 1px;
    color: var(--white);
  }
  .service {
    position: absolute;
    left: 54px;
    width: 593px;
    height: 128px;
    box-sizing: border-box;
    background: var(--box-fill);
    border: 2px solid var(--box-line);
  }
  .service-name {
    position: absolute;
    top: 0;
    height: 124px;
    line-height: 124px;
    font-size: 31px;
    color: var(--white);
    letter-spacing: 0.5px;
    white-space: nowrap;
  }
  .service-icon {
    position: absolute;
    border-radius: 8px;
  }
  .service--lawn { top: 170px; }
  .service--lawn .service-name { left: 58px; }
  .service--lawn .service-icon { left: 430px; top: 6px; width: 150px; height: 112px; background: linear-gradient(180deg, #ffffff 0%, #ffffff 60%, #2f8a3a 100%); }
  .service--washing { top: 325px; }
  .service--washing .service-name { left: 226px; }
  .service--washing .service-icon { left: 12px; top: 6px; width: 146px; height: 112px; background: linear-gradient(180deg, #ffffff 0%, #6b3a1e 40%, #4a2412 100%); }
  .service--gutter { top: 479px; }
  .service--gutter .service-name { left: 70px; }
  .service--gutter .service-icon { left: 420px; top: 8px; width: 158px; height: 108px; background: linear-gradient(135deg, #ffffff 0%, #d8f0d0 45%, #c8303a 100%); }
  .sender {
    position: absolute;
    left: 44px; top: 648px;
    width: 360px;
    text-align: center;
  }
  .sender-name {
    margin: 0;
    font-family: "PT Sans", Arial, sans-serif;
    font-weight: 700;
    font-size: 22px;
    line-height: 28px;
    color: var(--white);
  }
  .sender-phone {
    margin: 6px 0 0;
    font-family: "PT Sans", Arial, sans-serif;
    font-weight: 700;
    font-size: 28px;
    letter-spacing: 1px;
    color: var(--brand-red);
  }
  .brand-mark {
    position: absolute;
    left: 738px; top: 52px;
    width: 186px; height: 186px;
  }
  .brand-mark text {
    font-family: "PT Sans", Arial, sans-serif;
    font-weight: 700;
  }
  .stamp-box {
    position: absolute;
    left: 1024px; top: 29px;
    width: 176px; height: 141px;
    background: var(--white);
    display: flex;
    align-items: center;
    justify-content: center;
    font-family: "PT Serif", Georgia, serif;
    font-weight: 700;
    font-size: 18px;
    color: #111;
  }
  .address-block {
    position: absolute;
    left: 707px; top: 332px;
    width: 458px; height: 306px;
    background: var(--address-fill);
  }
  .address-line {
    position: absolute;
    left: 37px;
    width: 380px;
    height: 2px;
    background: var(--address-line);
  }
  .barcode-area {
    position: absolute;
    left: 525px; top: 676px;
    width: 675px; height: 103px;
    box-sizing: border-box;
    background: var(--white);
    border: 2px solid #222;
    display: flex;
    align-items: center;
    justify-content: center;
    font-family: "PT Sans", Arial, sans-serif;
    font-size: 30px;
    color: #111;
  }
</style>
</head>
<body>
<main class="postcard">
  <section class="services-panel">
    <h1 class="services-title">THE ADDITIONAL<br>SERVICES WE OFFER</h1>

    <div class="service service--lawn">
      <span class="service-name">LAWN MAINTANANCE</span>
      <div class="service-icon" role="img" aria-label="Illustration of a push lawn mower on grass"></div>
    </div>

    <div class="service service--washing">
      <div class="service-icon" role="img" aria-label="Illustration of a pressure washer wand cleaning a wooden fence"></div>
      <span class="service-name">PRESSURE WASHING</span>
    </div>

    <div class="service service--gutter">
      <span class="service-name">GUTTER CLEANING</span>
      <div class="service-icon" role="img" aria-label="Illustration of a cleaning bucket with a mop and cloth"></div>
    </div>

    <div class="sender">
      <p class="sender-name">Birchfield Lawn Pest Relief, LLC</p>
      <p class="sender-phone">404-555-0182</p>
    </div>
  </section>

  <section class="mailing-panel" aria-label="Mailing side"></section>

  <svg class="brand-mark" viewBox="0 0 186 186" aria-label="BLPR">
    <circle cx="93" cy="93" r="80" fill="none" stroke="#e0241b" stroke-width="16"/>
    <text x="93" y="103" text-anchor="middle" font-size="34" fill="#ffffff">BLPR</text>
  </svg>

  <div class="stamp-box">STAMP</div>

  <div class="address-block">
    <span class="address-line" style="top:62px"></span>
    <span class="address-line" style="top:126px"></span>
    <span class="address-line" style="top:190px"></span>
    <span class="address-line" style="top:251px"></span>
  </div>

  <div class="barcode-area">Barcode Area</div>
</main>
</body>
</html>
```